New Business Card Design for Manufacturing

We are an engineering/manufacturing company that offers Advanced machining/assembly/engineering services, as well as innovative products for the heavy duty engine cooling markets.

We are looking to get a new business card designed that is clean and modern looking, but still fits the wide range of technical/skilled work we do.

- We hope to use this design as the base for other design work in new Presentations, web, and print work.

Industry/Entity Type

Engineering

Contact Information for Business Card

Our preferred color of blue is (RGB) 22/71/159 but can vary slightly from that color. Our content will be our Logo and full company name (Vantrell Forge Works, Inc.), company address, name, job title, phone number with extension, cell number, fax number, website, and email address on the cards.
We'd like the full company name next to the logo, but we are open to other interpretations of that layout.
Preferably, we would like the back side to be clean with just our logo, and the front to contain all of the contact information.

Colors
2f74b4
0355a3
85abd2

Requirements
Must have
• - Logo, company name, needed content - We are open to interpretation beyond that.
• - Standard size business card.
• - Horizontal orientation.
• - Enough space for lengthy names / job titles (for example, a job title could read "Directory of Human Resources" or "V.P. of Governmental Affairs"). We need this to look clean, whether the title be short (CEO) or long (as described above).

```html
<!DOCTYPE html>
<html lang="en">
<head>
<meta charset="utf-8">
<title>Vantrell Forge Works – Business Card</title>
<link rel="stylesheet" href="https://fonts.googleapis.com/css2?family=Signika:wght@400;500;600&family=Open+Sans:wght@400&display=swap">
<style>
  :root {
    --brand-blue: #0e4e95;
    --brand-blue-deep: #0355a3;
    --ink: #3a3a3a;
    --card-black: #0b0b0c;
    --card-white: #f7f7f7;
    --steel-grey: #9a9ea3;
    --backdrop: #e4e4e4;
    --white: #ffffff;
  }
  html, body {
    margin: 0;
    padding: 0;
    width: 1200px;
    height: 576px;
    overflow: hidden;
    background: var(--backdrop);
  }
  .canvas {
    position: relative;
    width: 1200px;
    height: 576px;
  }
  .card {
    position: absolute;
    top: 138px;
    width: 482px;
    height: 293px;
    border-radius: 12px;
    overflow: hidden;
  }
  .card--back {
    left: 82px;
    background: var(--card-black);
    display: flex;
    align-items: center;
    justify-content: center;
  }
  .card--front {
    left: 603px;
    background: var(--card-white);
  }
  .wordmark {
    font-family: "Signika", sans-serif;
    font-weight: 600;
    margin: 0;
    line-height: 1.05;
  }
  .card--back .wordmark {
    color: var(--white);
    font-size: 40px;
    text-align: left;
  }
  .card--front .wordmark {
    position: absolute;
    right: 24px;
    top: 34px;
    color: var(--brand-blue);
    font-size: 30px;
    text-align: right;
  }
  .holder-name {
    position: absolute;
    left: 23px;
    top: 153px;
    margin: 0;
    font-family: "Signika", sans-serif;
    font-weight: 500;
    font-size: 21px;
    color: var(--brand-blue);
  }
  .holder-title {
    position: absolute;
    left: 23px;
    top: 178px;
    margin: 0;
    font-family: "Open Sans", sans-serif;
    font-size: 11px;
    color: var(--ink);
  }
  .title-rule {
    position: absolute;
    left: 131px;
    right: 24px;
    top: 188px;
    height: 1px;
    background: var(--brand-blue);
  }
  .contact-list {
    position: absolute;
    left: 23px;
    top: 203px;
    margin: 0;
    padding: 0;
    list-style: none;
    font-family: "Open Sans", sans-serif;
    font-size: 12px;
    color: var(--ink);
  }
  .contact-list li {
    display: flex;
    align-items: center;
    height: 17.5px;
  }
  .contact-list svg {
    width: 11px;
    height: 11px;
    margin-right: 9px;
    fill: var(--brand-blue);
  }
  .company-block {
    position: absolute;
    right: 24px;
    top: 197px;
    text-align: right;
  }
  .company-name {
    margin: 0 0 5px;
    font-family: "Signika", sans-serif;
    font-weight: 500;
    font-size: 14px;
    color: var(--brand-blue);
  }
  .company-address {
    margin: 0;
    font-family: "Open Sans", sans-serif;
    font-size: 12px;
    line-height: 18px;
    color: var(--ink);
  }
  .footer-bands {
    position: absolute;
    left: 0;
    bottom: 0;
    width: 482px;
    height: 30px;
  }
  .website {
    position: absolute;
    right: 24px;
    bottom: 6px;
    margin: 0;
    font-family: "Open Sans", sans-serif;
    font-size: 12px;
    color: var(--white);
  }
</style>
</head>
<body>
<main class="canvas">

  <section class="card card--back" aria-label="Card back">
    <p class="wordmark">Vantrell<br>Forge Works</p>
  </section>

  <section class="card card--front" aria-label="Card front">
    <p class="wordmark">Vantrell<br>Forge Works</p>

    <h1 class="holder-name">Marla Quinn Reyes</h1>
    <p class="holder-title">Managing Director</p>
    <div class="title-rule"></div>

    <ul class="contact-list">
      <li>
        <svg viewBox="0 0 12 12" aria-hidden="true"><path d="M1 4c0-2 2-3 5-3s5 1 5 3l-2 1-1-2H4L3 5zM3 6h6l1 5H2z"/></svg>
        555-0142-2200 (VFW)
      </li>
      <li>
        <svg viewBox="0 0 12 12" aria-hidden="true"><path d="M3 0h6a1 1 0 0 1 1 1v10a1 1 0 0 1-1 1H3a1 1 0 0 1-1-1V1a1 1 0 0 1 1-1zm0 2v7h6V2z"/></svg>
        555-0187-3310
      </li>
      <li>
        <svg viewBox="0 0 12 12" aria-hidden="true"><path d="M3 0h6v3H3zM1 4h10v5H9V7H3v2H1zM3 8h6v4H3z"/></svg>
        555-0163-4420
      </li>
      <li>
        <svg viewBox="0 0 12 12" aria-hidden="true"><path d="M0 2h12v1L6 7 0 3zM0 4.5l6 4 6-4V10H0z"/></svg>
        mreyes@vantrellforge.com
      </li>
    </ul>

    <div class="company-block">
      <p class="company-name">Vantrell Forge Works, Inc.</p>
      <p class="company-address">418 Millbrook Rd., Dayton Ridge,<br>OH 45402</p>
    </div>

    <svg class="footer-bands" viewBox="0 0 482 30" preserveAspectRatio="none" aria-hidden="true">
      <polygon points="0,18 250,18 250,30 0,30" fill="var(--steel-grey)"/>
      <polygon points="244,0 482,0 482,30 226,30" fill="var(--brand-blue-deep)"/>
    </svg>
    <p class="website">www.vantrellforge.com</p>
  </section>

</main>
</body>
</html>
```